For Lease Sign to Attract National Retail Tenants

Attached is a logo design that was created by Pixel Harbor. I will like to develop a leasing sign that is 4 foot wide by 4 foot high or 4 feet wide and 6 feet high. I would like the sign to have a black background and use the colors that are in the logo. These will be signs that are placed in front of shopping centers and are often read by passing motorist so the sign must be simple, clean, very easy to read, distinctive, and have as few words as possible. It would be good if small amounts of bright green can be added as a boarder or ????? The text should be FOR LEASE, 415-738-2916, Rod Kellaway. I will want to also design cards and letter head around the same theme.

Target Market(s)

National retail tenants wanting to lease space in my shopping centers

Industry/Entity Type

Real Estate Development

Contact Information for Business Card

Tall Oak Holdings, LLC Rod Kellaway President & CEO 4127 Marlow Ave. Suite 308 La Jolla, CA 92037 415-738-2916 rodkellaway@quillpost.net

```html
<!DOCTYPE html>
<html lang="en">
<head>
<meta charset="utf-8">
<title>For Lease – Tall Oak Holdings</title>
<link href="https://fonts.googleapis.com/css2?family=Montserrat:wght@600;700;800;900&display=swap" rel="stylesheet">
<style>
  :root {
    --wall-dark: #1e1e1e;
    --wall-mid: #3a3a3a;
    --wall-light: #4a4a4a;
    --skyline: #2f2f2f;
    --floor-light: #c9c9c9;
    --floor-dark: #7d7d7d;
    --brand-grey: #a9a9a9;
    --brand-red: #e0252b;
    --green-bright: #5cf02e;
    --green-deep: #0aa84a;
    --ink: #2e2e2e;
    --white: #ffffff;
    --panel-grey: #e6e6e6;
  }
  html, body {
    margin: 0;
    padding: 0;
    width: 1200px;
    height: 1200px;
    overflow: hidden;
    background: var(--wall-dark);
  }
  .sign {
    position: relative;
    width: 1200px;
    height: 1200px;
    overflow: hidden;
    font-family: "Montserrat", Arial, sans-serif;
    background: radial-gradient(ellipse at 50% 35%, var(--wall-light) 0%, var(--wall-mid) 45%, var(--wall-dark) 100%);
  }
  .brand {
    position: absolute;
    top: 250px;
    left: 0;
    width: 1200px;
    display: flex;
    justify-content: center;
    align-items: center;
    gap: 22px;
  }
  .brand-mark {
    width: 34px;
    height: 34px;
    background: var(--brand-red);
  }
  .brand-name {
    font-weight: 700;
    font-size: 46px;
    letter-spacing: 1px;
    color: var(--brand-grey);
    text-transform: uppercase;
  }
  .headline {
    position: absolute;
    top: 400px;
    left: 0;
    width: 1200px;
    height: 340px;
  }
  .skyline {
    position: absolute;
    left: 0;
    top: 830px;
    width: 1200px;
    height: 180px;
    background: linear-gradient(180deg, rgba(47,47,47,0) 0%, var(--skyline) 30%, var(--skyline) 100%);
  }
  .floor {
    position: absolute;
    left: 0;
    top: 1000px;
    width: 1200px;
    height: 200px;
    background: linear-gradient(180deg, var(--floor-dark) 0%, var(--floor-light) 45%, #b4b4b4 100%);
  }
  .call-us {
    position: absolute;
    top: 818px;
    left: 0;
    width: 1200px;
    text-align: center;
    font-weight: 700;
    font-size: 44px;
    letter-spacing: 24px;
    color: var(--white);
  }
  .phone-backer {
    position: absolute;
    left: 290px;
    top: 905px;
    width: 735px;
    height: 185px;
    background: var(--panel-grey);
    clip-path: polygon(0 18%, 100% 0, 100% 100%, 0 100%);
    transform: rotate(-2deg);
  }
  .phone-panel {
    position: absolute;
    left: 222px;
    top: 915px;
    width: 695px;
    height: 130px;
    background: var(--green-bright);
    transform: rotate(-2.5deg);
    display: flex;
    align-items: center;
    justify-content: center;
    box-shadow: 0 6px 10px rgba(0,0,0,0.25);
  }
  .phone-number {
    font-weight: 800;
    font-size: 98px;
    letter-spacing: -2px;
    color: var(--ink);
  }
  .contact-name {
    position: absolute;
    left: 308px;
    top: 1062px;
    width: 565px;
    height: 74px;
    background: var(--green-deep);
    clip-path: polygon(5% 0, 95% 0, 100% 50%, 95% 100%, 5% 100%, 0 50%);
    display: flex;
    align-items: center;
    justify-content: center;
    font-weight: 700;
    font-size: 50px;
    letter-spacing: 1px;
    color: var(--white);
  }
</style>
</head>
<body>
<main class="sign">
  <div class="brand">
    <span class="brand-mark"></span>
    <span class="brand-name">Tall Oak Holdings, LLC</span>
  </div>

  <svg class="headline" viewBox="0 400 1200 340" width="1200" height="340" aria-label="For Lease">
    <defs>
      <linearGradient id="chrome" x1="0" y1="0" x2="0" y2="1">
        <stop offset="0" stop-color="#f4f4f4"/>
        <stop offset="0.45" stop-color="#ffffff"/>
        <stop offset="0.55" stop-color="#bdbdbd"/>
        <stop offset="1" stop-color="#e8e8e8"/>
      </linearGradient>
      <radialGradient id="sticker" cx="0.4" cy="0.35" r="0.7">
        <stop offset="0" stop-color="#8dff5a"/>
        <stop offset="0.6" stop-color="#33c61f"/>
        <stop offset="1" stop-color="#138a12"/>
      </radialGradient>
    </defs>
    <text class="lease-word" x="120" y="708" textLength="960" lengthAdjust="spacingAndGlyphs"
          font-family="Montserrat, Arial, sans-serif" font-weight="900" font-size="350"
          fill="url(#chrome)" stroke="#1b1b2a" stroke-width="6" paint-order="stroke">LEASE</text>
    <circle class="for-sticker-edge" cx="297" cy="490" r="80" fill="#ffffff"/>
    <circle class="for-sticker" cx="297" cy="490" r="70" fill="url(#sticker)"/>
    <text class="for-word" x="292" y="516" text-anchor="middle"
          font-family="Montserrat, Arial, sans-serif" font-weight="800" font-size="70"
          fill="#2a2a2a" letter-spacing="-3">FOR</text>
  </svg>

  <div class="skyline" role="img" aria-label="City skyline silhouette"></div>
  <div class="floor" role="img" aria-label="Weathered grey wooden floorboards"></div>

  <div class="call-us">CALL US:</div>
  <div class="phone-backer"></div>
  <div class="phone-panel"><span class="phone-number">415-738-2916</span></div>
  <div class="contact-name">ROD KELLAWAY</div>
</main>
</body>
</html>
```